Beacon Advisory Website

I currently have a website www.beaconadvisoryinc.com. We are a IT Consulting Company. Our website will pretty much tell out our services. I am looking to enhance my website and make it look more professional. Looking for very classy and Contemporary look and design for my website.

It Company

```html
<!DOCTYPE html>
<html lang="en">
<head>
<meta charset="utf-8">
<title>Beacon Advisory</title>
<link href="https://fonts.googleapis.com/css2?family=Open+Sans:wght@400;600;700&display=swap" rel="stylesheet">
<style>
:root{
  --blue:#1a9ad9;
  --blue-dark:#1a5a9a;
  --navy:#0f3d73;
  --ink:#222a33;
  --text:#666c73;
  --band:#1da3e3;
  --foot-top:#1ca0e0;
  --foot-bottom:#1670c2;
  --bar:#1a63b0;
  --white:#fff;
  --light:#f2f3f5;
}
*{margin:0;padding:0;box-sizing:border-box}
html,body{width:714px;height:1200px;overflow:hidden}
body{font-family:"Open Sans",Arial,sans-serif;color:var(--text);background:var(--white);position:relative}
.abs{position:absolute}
.header{top:0;left:0;width:714px;height:45px;background:var(--white);border-top:2px solid var(--blue);box-shadow:0 1px 3px rgba(0,0,0,.08);z-index:2}
.brand{display:flex;align-items:center;gap:6px;font-weight:700;color:var(--blue-dark)}
.brand-mark{width:14px;height:14px;background:var(--blue-dark);border-radius:3px}
.header .brand{position:absolute;left:96px;top:13px;font-size:12px}
.nav{position:absolute;left:312px;top:-2px;display:flex;height:47px}
.nav a{display:flex;align-items:center;padding:0 10px;font-size:6.5px;font-weight:600;color:var(--ink);text-decoration:none;letter-spacing:.2px}
.nav a.active{background:var(--blue);color:var(--white);width:50px;justify-content:center;padding:0}
.hero{top:45px;left:0;width:714px;height:300px;background:linear-gradient(90deg,#eef4fa 0%,#dce8f3 45%,#7d93ad 68%,#2d3f5c 88%,#1f2c44 100%)}
.hero-title{left:96px;top:141px;font-size:16.5px;font-weight:600;color:#1e5a8c;display:flex;align-items:center;gap:8px}
.hero-title .brand-mark{width:20px;height:20px;background:var(--blue)}
.hero-title b{color:var(--blue);font-weight:600}
.hero-text{left:96px;top:173px;width:235px;font-size:7px;line-height:13px;color:#5a6470}
.btn{display:inline-block;background:var(--blue);color:var(--white);font-size:6.5px;font-weight:700;padding:0 9px;height:24px;line-height:24px}
.hero .btn,.welcome .btn{position:absolute}
.arrow{width:20px;height:20px;border:1.5px solid rgba(255,255,255,.85);border-radius:50%;top:180px}
.welcome-bg{top:345px;left:398px;width:316px;height:205px;background:var(--light);clip-path:polygon(35px 0,100% 0,100% 100%,0 100%)}
.section-title{font-size:12.5px;font-weight:700;color:var(--ink);display:flex;align-items:center;gap:6px}
.section-title .brand-mark{width:14px;height:14px}
.section-title b{color:var(--blue)}
.welcome-title{left:96px;top:381px}
.welcome-text{left:96px;top:411px;width:314px;font-size:5.6px;line-height:11.5px;color:#555}
.devices{left:440px;top:390px;width:178px;height:116px;background:linear-gradient(135deg,#b9cde0,#5b7fa8 55%,#2a3a52);border-radius:4px}
.band{top:550px;left:0;width:714px;height:224px;background:var(--band)}
.card{top:584px;width:162px;height:155px;background:var(--white);text-align:center;box-shadow:0 2px 6px rgba(0,0,0,.1)}
.card svg{margin-top:17px}
.card h3{font-size:8.5px;font-weight:600;color:var(--ink);margin-top:8px;letter-spacing:.3px}
.card p{font-size:5.8px;line-height:11.2px;margin:6px 14px 0;color:#777}
.card a{display:block;font-size:6.2px;font-weight:700;color:var(--blue-dark);margin-top:6px;text-decoration:none}
.blog-title{left:0;width:714px;top:792px;justify-content:center}
.post{top:827px;width:162px}
.post-img{height:90px;border:2px solid #e3e6ea}
.post h4{font-size:8.3px;font-weight:600;color:var(--blue);margin-top:9px}
.post p{font-size:5.8px;line-height:11.5px;margin-top:4px;color:#666}
.meta{font-size:6px;color:var(--blue-dark);margin-top:6px;display:flex;gap:6px;align-items:center}
.meta span{display:flex;align-items:center;gap:2px}
.footer{top:1030px;left:0;width:714px;height:132px;background:linear-gradient(180deg,var(--foot-top),var(--foot-bottom))}
.footer .brand{position:absolute;left:96px;top:30px;color:var(--white);font-size:12px}
.footer .brand-mark{background:var(--white)}
.foot-about{left:96px;top:49px;width:115px;font-size:6px;line-height:11px;color:var(--white)}
.foot-about a{display:block;font-weight:600;margin-top:4px;color:var(--white);text-decoration:none}
.foot-col{top:35px;font-size:6.4px;color:#e6f3fb}
.foot-col h5{font-size:8.5px;font-weight:600;color:var(--white);margin-bottom:6px;letter-spacing:.3px}
.foot-col li{list-style:none;line-height:13.4px}
.foot-col p{line-height:11px;margin-bottom:6px}
.email{width:144px;height:20px;background:var(--white);border-radius:2px;font-size:6px;color:#666;padding-left:8px;line-height:20px}
.subscribe{margin-top:9px;width:61px;height:22px;background:var(--navy);color:var(--white);font-size:7px;font-weight:700;line-height:22px;text-align:center}
.bottom{top:1162px;left:0;width:714px;height:38px;background:var(--bar)}
.copy{left:96px;top:14px;font-size:6px;color:#e6f0fa}
.social{left:520px;top:10px;display:flex;gap:2px}
.social i{width:18px;height:18px;border:1.3px solid var(--white);border-radius:50%}
</style>
</head>
<body>

<header class="header abs">
  <div class="brand"><span class="brand-mark"></span>BEACON ADVISORY</div>
  <nav class="nav">
    <a class="active">COMPANY</a><a>SERVICES</a><a>SOLUTIONS</a><a>RESOURCES</a><a>CAREER</a><a>CONTACT US</a>
  </nav>
</header>

<section class="hero abs" role="img" aria-label="Photo of two businessmen in suits reviewing documents together">
  <div class="arrow abs" style="left:21px"></div>
  <div class="arrow abs" style="left:669px"></div>
</section>
<h1 class="hero-title abs"><span class="brand-mark"></span><span><b>BEACON</b> ADVISORY</span></h1>
<p class="hero-text abs">Sed ut loerspiciatis unde omnis iste natus error sit volup tatem accus antium dolore mq uloe laud antium, tota m rem aperiam, eaque ipsa quae abSed ut p loerspiciatis unde omnis iste natus</p>
<a class="btn abs" style="left:96px;top:223px">READ MORE ›</a>

<div class="welcome-bg abs"></div>
<h2 class="section-title welcome-title abs"><span class="brand-mark" style="background:var(--blue-dark)"></span><span>WELCOME TO <b>BEACON ADVISORY</b></span></h2>
<p class="welcome-text abs">Today's IT market is a dynamic, fast-paced industry, with ever-increasing demands. Meeting these demands for over 25 years, Beacon Advisory maintains a global presence, aggressively recruiting expertly qualified IT and Management Professionals from around the world and cultivating key partnerships with corporations to understand their business models end-to-end, with a goal of delivering exceptional client service and ensuring a consistent delivery of the talent needed to drive results.</p>
<a class="btn abs" style="left:96px;top:481px;background:var(--blue-dark)">READ MORE ›</a>
<div class="devices abs" role="img" aria-label="Desktop, tablet and phone showing the website with a city office skyline"></div>

<section class="band abs"></section>
<div class="card abs" style="left:96px">
  <svg width="50" height="50" viewBox="0 0 50 50"><circle cx="25" cy="25" r="25" fill="#1a5a9a"/><rect x="14" y="15" width="22" height="15" fill="none" stroke="#fff" stroke-width="1.8"/><path d="M18 27v-4M22 27v-6M26 27v-3M30 27v-8" stroke="#fff" stroke-width="2"/><path d="M22 34h6M25 30v4" stroke="#fff" stroke-width="1.8"/></svg>
  <h3>CONSULTING</h3>
  <p>Sed ut perspiciatis unde omnis isnatus error sitatem accolosa ntium doloremque mined ut perspiciatis unde omnis isnatus lorem.</p>
  <a>READ MORE</a>
</div>
<div class="card abs" style="left:276px">
  <svg width="50" height="50" viewBox="0 0 50 50"><circle cx="25" cy="25" r="25" fill="#1a5a9a"/><circle cx="25" cy="20" r="4" fill="#fff"/><circle cx="17" cy="22" r="3" fill="#fff"/><circle cx="33" cy="22" r="3" fill="#fff"/><path d="M18 33a7 7 0 0 1 14 0z" fill="#fff"/><path d="M11 32a6 6 0 0 1 9-4v4zM39 32a6 6 0 0 0-9-4v4z" fill="#fff"/></svg>
  <h3>STAFF AUGMENTATION</h3>
  <p>Sed ut perspiciatis unde omnis isnatus error sitatem accolosa ntium doloremque mined ut perspiciatis unde omnis isnatus lorem.</p>
  <a>READ MORE</a>
</div>
<div class="card abs" style="left:455px">
  <svg width="50" height="50" viewBox="0 0 50 50"><circle cx="25" cy="25" r="25" fill="#1a5a9a"/><g fill="none" stroke="#fff" stroke-width="1.8"><circle cx="25" cy="26" r="13"/><circle cx="25" cy="26" r="8.5"/><circle cx="25" cy="26" r="4"/><path d="M25 26l11-11M32 14h5v5"/></g></svg>
  <h3>OFFSHORE</h3>
  <p>Sed ut perspiciatis unde omnis isnatus error sitatem accolosa ntium doloremque mined ut perspiciatis unde omnis isnatus lorem.</p>
  <a>READ MORE</a>
</div>

<h2 class="section-title blog-title abs"><span class="brand-mark" style="background:var(--blue-dark)"></span><span>LATEST <b>BLOG NEWS</b></span></h2>
<article class="post abs" style="left:96px">
  <div class="post-img" role="img" aria-label="Hands using a tablet at an office desk" style="background:linear-gradient(135deg,#cfe0f0,#8fb0d0)"></div>
  <h4>Lorem ipsum dolor sit amet, conse</h4>
  <p>Sed ut p loerspiciatis unde omnis iste natus error sit volup tatem accusantium dolore mq uloe laud antium, tota m rem aperiam, eaque ipsa quae ab.</p>
  <div class="meta"><span>▦ March 05 2015</span><span>● Comments</span></div>
</article>
<article class="post abs" style="left:276px">
  <div class="post-img" role="img" aria-label="Colleagues shaking hands in a bright office" style="background:linear-gradient(135deg,#d8c2a8,#7d8a9c 60%,#34404f)"></div>
  <h4>Lorem ipsum dolor sit amet, conse</h4>
  <p>Sed ut p loerspiciatis unde omnis iste natus error sit volup tatem accusantium dolore mq uloe laud antium, tota m rem aperiam, eaque ipsa quae ab.</p>
  <div class="meta"><span>▦ March 05 2015</span><span>● Comments</span></div>
</article>
<article class="post abs" style="left:455px">
  <div class="post-img" role="img" aria-label="Two hands joining puzzle pieces" style="background:linear-gradient(135deg,#f0dcc8,#c99c7c 55%,#8a5a44)"></div>
  <h4>Lorem ipsum dolor sit amet, conse</h4>
  <p>Sed ut p loerspiciatis unde omnis iste natus error sit volup tatem accusantium dolore mq uloe laud antium, tota m rem aperiam, eaque ipsa quae ab.</p>
  <div class="meta"><span>▦ March 05 2015</span><span>● Comments</span></div>
</article>

<footer class="footer abs">
  <div class="brand"><span class="brand-mark"></span>BEACON ADVISORY</div>
  <p class="foot-about abs">Sed ut perspiciatis unde omnis isten error sit voluptatem accusantiloudo emq ue laudantiu totavoluptat.<a>READ MORE</a></p>
  <div class="foot-col abs" style="left:254px">
    <h5>RESOURCES</h5>
    <ul><li>Support</li><li>Security Center</li><li>Developer Center</li><li>Privacy Policy</li><li>Legal</li></ul>
  </div>
  <div class="foot-col abs" style="left:364px">
    <h5>SUPPORT</h5>
    <ul><li>FAQs</li><li>Privacy Policy</li><li>Recommendations</li><li>Contact</li></ul>
  </div>
  <div class="foot-col abs" style="left:473px">
    <h5>SIGN UP NEWSLETTER</h5>
    <p>Please sign up here for latest deals</p>
    <div class="email">Email address</div>
    <div class="subscribe">SUBSCRIBE</div>
  </div>
</footer>

<div class="bottom abs">
  <p class="copy abs">© 2016 beaconadvisoryinc.com. All copyrights are reserved &nbsp;Term of Use</p>
  <div class="social abs"><i></i><i></i><i></i><i></i><i></i></div>
</div>

</body>
</html>
```